Real Estate Sign to Help Modernize and Make it POP!

Design a sign style that would be good for marketing the sale or lease of properties. This will be 3 ' x 4' when printed and needs to look professional, modern, and catchy. It should us the company name, logo, and phone number at a minimum. Keep with the color scheme but open to varieties.

It will be printed and put in a large wooden frame as shown in one of the pictures.

Target Market(s)

Buyers and Tenants

Industry/Entity Type

Real Estate

Requirements
Must have
• company name, logo, and phone number
same color scheme as sign and website
Nice to have
• My Name, "Mervin Kalloway, CCIM"
Company Website
Ability to have an easy change from FOR SALE to FOR LEASE or FOR SALE/LEASE when I need to move this sign to a new property
An ability to have reflective colors printed on the contrast for cars to see at night
Should not have
• "Property Managed by"

```html
<!DOCTYPE html>
<html lang="en">
<head>
<meta charset="utf-8">
<title>Meridian Crest Realty – For Sale / For Lease Sign</title>
<link href="https://fonts.googleapis.com/css2?family=Marcellus&family=Tinos:wght@400;700&family=Rubik:wght@500&display=swap" rel="stylesheet">
<style>
  :root {
    --teal: #3f5d57;
    --teal-dark: #34504a;
    --sage: #a9b995;
    --ink: #2b2b2b;
    --name-grey: #545454;
    --paper: #ffffff;
    --backdrop: #f4f4f2;
    --leaf-light: #9cc27a;
    --leaf-mid: #5f8a3f;
    --leaf-deep: #3a5a2a;
  }
  html, body {
    margin: 0;
    padding: 0;
    width: 901px;
    height: 1200px;
    overflow: hidden;
    background: var(--backdrop);
  }
  .canvas {
    position: relative;
    width: 901px;
    height: 1200px;
  }
  .sign-frame {
    position: absolute;
    left: 30px;
    top: 285px;
    width: 840px;
    height: 630px;
    box-shadow: 0 3px 10px rgba(0,0,0,0.25);
  }
  .sign {
    position: absolute;
    left: 0;
    top: 0;
    width: 1020px;
    height: 765px;
    transform: scale(0.8235);
    transform-origin: 0 0;
    background: var(--paper);
    overflow: hidden;
  }
  .sign-art {
    position: absolute;
    left: 0;
    top: 0;
    width: 1020px;
    height: 765px;
  }
  .brand {
    position: absolute;
    left: 45px;
    width: 360px;
    text-align: center;
    font-family: "Marcellus", serif;
    color: var(--teal);
    font-size: 40px;
    letter-spacing: 3px;
    line-height: 46px;
  }
  .brand-mark {
    position: absolute;
    left: 170px;
    top: 40px;
    width: 110px;
    height: 110px;
    border-radius: 50%;
    background: var(--teal);
  }
  .agent-name {
    position: absolute;
    left: 45px;
    top: 300px;
    width: 400px;
    font-family: "Tinos", serif;
    font-size: 50px;
    color: var(--name-grey);
    white-space: nowrap;
  }
  .agent-title {
    position: absolute;
    left: 45px;
    top: 360px;
    width: 360px;
    text-align: center;
    font-family: "Tinos", serif;
    font-weight: 700;
    font-size: 78px;
    line-height: 78px;
    color: var(--sage);
  }
  .status {
    position: absolute;
    left: 45px;
    top: 470px;
    font-family: "Tinos", serif;
    color: var(--paper);
    font-size: 82px;
    line-height: 78px;
    white-space: nowrap;
  }
  .status strong { font-weight: 700; }
  .contact {
    position: absolute;
    left: 45px;
    top: 668px;
    display: flex;
    align-items: center;
    font-family: "Rubik", sans-serif;
    font-weight: 500;
    font-size: 36px;
    color: var(--ink);
    white-space: nowrap;
  }
  .contact-icon {
    width: 32px;
    height: 32px;
    margin-right: 14px;
  }
  .contact-phone { margin-right: 30px; }
</style>
</head>
<body>
<div class="canvas">
  <div class="sign-frame">
    <div class="sign">
      <svg class="sign-art" viewBox="0 0 1020 765" xmlns="http://www.w3.org/2000/svg">
        <defs>
          <clipPath id="sign-clip"><rect x="0" y="0" width="1020" height="765"/></clipPath>
          <linearGradient id="property-photo-tones" x1="0" y1="0" x2="0.3" y2="1">
            <stop offset="0" stop-color="var(--leaf-mid)"/>
            <stop offset="0.45" stop-color="var(--leaf-deep)"/>
            <stop offset="0.8" stop-color="var(--leaf-mid)"/>
            <stop offset="1" stop-color="var(--leaf-light)"/>
          </linearGradient>
        </defs>
        <g clip-path="url(#sign-clip)">
          <rect class="status-band" x="0" y="452" width="1020" height="198" fill="var(--teal)"/>
          <circle class="photo-rim" cx="862" cy="225" r="448" fill="var(--teal-dark)"/>
          <circle class="property-photo" cx="882" cy="230" r="440" fill="url(#property-photo-tones)" role="img" aria-label="Photo of the listed property: a columned house beneath large live oak trees on a green lawn"/>
          <rect class="footer-strip" x="0" y="650" width="1020" height="115" fill="var(--paper)"/>
        </g>
      </svg>

      <div class="brand-mark" aria-hidden="true"></div>
      <div class="brand" style="top:190px;">MERIDIAN CREST<br>REALTY</div>

      <div class="agent-name">Mervin Kalloway</div>
      <div class="agent-title">CCIM</div>

      <div class="status">FOR <strong>SALE</strong><br>FOR <strong>LEASE</strong></div>

      <div class="contact">
        <svg class="contact-icon" viewBox="0 0 24 24" aria-hidden="true">
          <path d="M6.6 3.5l2.6 3.4-1.6 2.2c.9 2.2 2.8 4.4 5.2 5.6l2.1-1.7 3.5 2.4-1.4 3.4C11 18.8 4.9 12.3 4.3 5z" fill="none" stroke="var(--teal)" stroke-width="1.8" stroke-linejoin="round"/>
          <path d="M14 3.5a7 7 0 0 1 6.5 6.5M14 6.8a3.8 3.8 0 0 1 3.3 3.3" fill="none" stroke="var(--teal)" stroke-width="1.6" stroke-linecap="round"/>
        </svg>
        <span class="contact-phone">(555) 214-7730</span>
        <svg class="contact-icon" viewBox="0 0 24 24" aria-hidden="true">
          <circle cx="12" cy="12" r="9" fill="none" stroke="var(--teal)" stroke-width="1.6"/>
          <ellipse cx="12" cy="12" rx="4" ry="9" fill="none" stroke="var(--teal)" stroke-width="1.4"/>
          <path d="M3 12h18M4.5 7.5h15M4.5 16.5h15M12 3v18" stroke="var(--teal)" stroke-width="1.3"/>
        </svg>
        <span class="contact-web">www.meridiancrestrealty.com</span>
      </div>
    </div>
  </div>
</div>
</body>
</html>
```